Brightmill Data Works

Our company is about IT hardwares and IT solutions. IT hardware such as PC, RAMS, storage and servers. IT solutions such as project management, BA. We are also selling new technology too.

Target Market(s)

Consumer, Small to Medium Business, Corporate

Requirements
Must have
• The business card must have the following:
• Name:
• Title:
• Contact Number:
• Email address:
• Website:
• Color: Must match the logo color upgrade

```html
<!DOCTYPE html>
<html lang="en">
<head>
<meta charset="utf-8">
<title>Brightmill Data Works – Business Card</title>
<link rel="stylesheet" href="https://fonts.googleapis.com/css2?family=Rajdhani:wght@700&family=Roboto:wght@400;500&family=Roboto+Condensed:wght@400;500&display=swap">
<style>
  :root {
    --backdrop: #dedede;
    --card-light: #f7f7f6;
    --card-dark: #454545;
    --ink: #454545;
    --accent: #d08a2c;
    --accent-faint: rgba(214, 150, 80, 0.13);
    --accent-faint-dark: rgba(214, 150, 80, 0.16);
    --white: #ffffff;
  }
  * { margin: 0; padding: 0; box-sizing: border-box; }
  html, body {
    width: 1200px; height: 960px; overflow: hidden;
    background: var(--backdrop);
  }
  .canvas { position: relative; width: 1200px; height: 960px; }
  .card {
    position: absolute; width: 600px; height: 343px; overflow: hidden;
  }
  .card--front { left: 314px; top: 113px; background: var(--card-light); }
  .card--back { left: 311px; top: 472px; background: var(--card-dark); }

  .decor-circle {
    position: absolute; width: 360px; height: 360px; border-radius: 50%;
    left: 330px; top: 20px; background: var(--accent-faint);
  }
  .card--back .decor-circle { background: var(--accent-faint-dark); left: 327px; top: 0; }

  .brand {
    position: absolute; left: 48px; top: 100px;
    display: flex; align-items: center; gap: 10px;
  }
  .brand__mark { width: 14px; height: 14px; background: var(--accent); }
  .brand__name {
    font-family: "Rajdhani", sans-serif; font-weight: 700;
    font-size: 31px; letter-spacing: 0.5px; color: var(--ink);
    text-transform: uppercase; line-height: 1;
  }

  .contact {
    position: absolute; left: 49px; top: 241px; list-style: none;
    font-family: "Roboto", sans-serif; font-size: 14px; color: var(--ink);
  }
  .contact__item { display: flex; align-items: center; gap: 7px; height: 19.5px; }
  .contact__icon { width: 12px; height: 12px; fill: var(--ink); flex: none; }

  .person {
    position: absolute; right: 61px; top: 243px; text-align: right;
  }
  .person__name {
    font-family: "Roboto Condensed", sans-serif; font-weight: 500;
    font-size: 27px; color: var(--ink); line-height: 1; text-transform: uppercase;
  }
  .person__title {
    margin-top: 4px;
    font-family: "Roboto", sans-serif; font-weight: 500;
    font-size: 14px; color: var(--accent); letter-spacing: 0.3px;
  }

  .back__rule {
    position: absolute; left: 42px; top: 270px; width: 516px; height: 3px;
    background: var(--accent);
  }
  .back__url {
    position: absolute; left: 43px; top: 279px;
    font-family: "Roboto", sans-serif; font-weight: 500;
    font-size: 16px; color: var(--white);
  }
</style>
</head>
<body>
<main class="canvas">
  <section class="card card--front" aria-label="Business card front">
    <div class="decor-circle"></div>
    <div class="brand">
      <span class="brand__mark"></span>
      <span class="brand__name">Brightmill Data Works</span>
    </div>
    <ul class="contact">
      <li class="contact__item">
        <svg class="contact__icon" viewBox="0 0 24 24"><path d="M6.6 10.8c1.4 2.8 3.8 5.1 6.6 6.6l2.2-2.2c.3-.3.7-.4 1-.2 1.1.4 2.3.6 3.6.6.6 0 1 .4 1 1V20c0 .6-.4 1-1 1C10.6 21 3 13.4 3 4c0-.6.4-1 1-1h3.5c.6 0 1 .4 1 1 0 1.3.2 2.5.6 3.6.1.3 0 .7-.2 1L6.6 10.8z"/></svg>
        555 210 4876
      </li>
      <li class="contact__item">
        <svg class="contact__icon" viewBox="0 0 24 24"><path d="M2 5h20v14H2z M4 7v.5l8 5 8-5V7l-8 5z" fill-rule="evenodd"/></svg>
        daniel@brightmilldata.com
      </li>
      <li class="contact__item">
        <svg class="contact__icon" viewBox="0 0 24 24"><circle cx="12" cy="12" r="10"/><path d="M7 8c2 0 3 1 3 3s-2 2-2 4l-2 1M15 4c-1 2 0 3 2 3s2 2 1 3-3 1-3 3 1 4 1 4" stroke="#f7f7f6" stroke-width="1.6" fill="none"/></svg>
        www.brightmilldata.com
      </li>
    </ul>
    <div class="person">
      <p class="person__name">Daniel Harrow</p>
      <p class="person__title">CEO/FOUNDER</p>
    </div>
  </section>

  <section class="card card--back" aria-label="Business card back">
    <div class="decor-circle"></div>
    <div class="back__rule"></div>
    <p class="back__url">www.brightmilldata.com</p>
  </section>
</main>
</body>
</html>
```